Creative Web design for Tattoo Artist

I am a tattoo artist with a private tattoo/art studio in Spring, TX. I need to design a website for my studio, to include the following "pages" :
-home/about
-FAQ
-Gallery
-Inquiries
-shop
We would like to see designs that are more dark or "moody", and like the colors black/gold.
I'd like my website to reflect my studio, an award winning private, upscale custom only tattoo studio.

I've attached some examples of styles we liked.

Target Market(s)

adults ages 18-50, interested in tattoos, or fine art

Industry/Entity Type

Tattoos/Fine Art/Arts

Coding

Coded - Design and coding required

Number of Pages Required

5+ page

Colors

Designer to choose colors to be used in the design.

Requirements
Must have
• gallery section, and e-commerce page set up so I can begin selling merchandise, I'd like the fonts to flow with my logo design

```html
<!DOCTYPE html>
<html lang="en">
<head>
<meta charset="utf-8">
<title>The Gilded Viper — Custom Tattoo Studio</title>
<link rel="stylesheet" href="https://fonts.googleapis.com/css2?family=Lora:wght@500;700&family=Roboto:wght@400;500;700&display=swap">
<style>
:root{
  --black:#000;
  --footer:#0e0e0e;
  --gold:#b5802a;
  --gold-dark:#a86f1f;
  --gold-light:#c9962f;
  --white:#fff;
  --text:#d6d6d6;
  --rule:#3a3a3a;
}
*{margin:0;padding:0;box-sizing:border-box}
html,body{width:1200px;height:3597px;overflow:hidden;background:var(--black)}
body{position:relative;font-family:"Roboto",sans-serif;color:var(--white)}
.abs{position:absolute}
.serif{font-family:"Lora",serif}

/* header */
.site-header{position:absolute;left:0;top:0;width:1200px;height:112px;background:var(--black);z-index:3}
.brand-badge{position:absolute;left:66px;top:-9px;width:168px;height:202px;border-radius:0 0 84px 84px;background:var(--black);z-index:4;display:flex;align-items:center;justify-content:center;text-align:center}
.brand-badge span{font-family:"Lora",serif;font-weight:700;font-size:17px;line-height:1.25;letter-spacing:1px;color:var(--white)}
.main-nav a{position:absolute;top:47px;font-size:14px;font-weight:700;color:var(--white);text-decoration:none;letter-spacing:.2px}
.nav-contact{position:absolute;left:840px;top:32px;width:122px;height:48px;border:2px solid var(--gold);display:flex;align-items:center;justify-content:center;font-size:14px;font-weight:700}
.header-icon{position:absolute;top:42px}

/* hero */
.hero-visual{position:absolute;left:0;top:112px;width:1200px;height:514px;background:radial-gradient(ellipse at 40% 55%,#4a3d34 0%,#2a2522 40%,#111 80%)}
.hero-title{position:absolute;left:594px;top:266px;font-family:"Lora",serif;font-weight:700;font-size:48px;line-height:58px;color:var(--white)}
.btn-quote{position:absolute;left:596px;top:413px;width:140px;height:47px;background:var(--gold);display:flex;align-items:center;justify-content:center;font-size:14px;font-weight:700}
.slider-dot{position:absolute;left:588px;top:595px;width:7px;height:7px;background:var(--white);transform:rotate(45deg)}
.social-rail .diamond{position:absolute;left:1131px;top:290px;width:27px;height:27px;border:1.5px solid var(--white);transform:rotate(45deg)}
.social-rail .sq{position:absolute;left:1139px;width:10px;height:10px;background:var(--white);border-radius:50%}
.scroll-line{position:absolute;left:1144px;top:426px;width:1px;height:70px;background:var(--white)}
.scroll-label{position:absolute;left:1100px;top:550px;width:90px;font-size:10px;font-weight:500;transform:rotate(-90deg);text-align:center;letter-spacing:.5px}

/* story sections */
.section-title{position:absolute;font-family:"Lora",serif;font-weight:500;font-size:36px;color:var(--white);letter-spacing:.5px}
.copy{position:absolute;width:498px;font-size:16px;line-height:27.5px;color:var(--text);text-align:justify}
.copy p+p{margin-top:13px}
.learn-more{position:absolute;display:flex;align-items:center;gap:12px;font-size:14px;font-weight:700}
.gold-frame{position:absolute;border:3px solid var(--gold)}
.photo{position:absolute}

/* products */
.products-band{position:absolute;left:0;top:1957px;width:1200px;height:557px;background:
  radial-gradient(circle at 10% 90%,rgba(210,120,40,.35) 0 18%,transparent 19%),
  radial-gradient(circle at 85% 20%,rgba(150,95,20,.3) 0 14%,transparent 15%),
  linear-gradient(180deg,var(--gold-dark) 0%,var(--gold-light) 55%,#c27a22 100%)}
.product-card{position:absolute;top:2107px;width:231px;height:273px;background:var(--white);display:flex;align-items:center;justify-content:center}
.product-card .garment{width:150px;height:185px;background:linear-gradient(180deg,#2a2a2a,#0f0f0f);border-radius:18px 18px 6px 6px}
.product-name{position:absolute;top:2402px;width:231px;text-align:center;font-size:16px;font-weight:500;color:var(--white)}
.product-price{position:absolute;top:2430px;width:231px;text-align:center;font-size:16px;font-weight:700;color:var(--white)}

/* footer */
.site-footer{position:absolute;left:0;top:3199px;width:1200px;height:398px;background:var(--footer)}
.footer-nav a{position:absolute;top:3279px;font-size:14px;font-weight:700;color:var(--white);text-decoration:none}
.hr{position:absolute;height:1px;background:var(--rule)}
.vr{position:absolute;width:1px;background:var(--rule)}
.contact-col{position:absolute;width:320px;text-align:center}
.contact-col h4{font-size:16px;font-weight:700;margin:10px 0 8px}
.contact-col p{font-size:14px;line-height:24px;color:var(--text)}
.footer-brand{position:absolute;left:540px;top:3262px;width:120px;text-align:center;font-family:"Lora",serif;font-weight:700;font-size:15px;line-height:1.3;letter-spacing:1px}
.copyright{position:absolute;left:0;top:3559px;width:1200px;text-align:center;font-size:10px;color:var(--text)}
.copyright b{color:var(--white)}
.foot-social{position:absolute;top:3554px;width:24px;height:24px;transform:rotate(45deg)}
</style>
</head>
<body>

<header class="site-header">
  <nav class="main-nav">
    <a href="#" style="left:411px">ABOUT</a>
    <a href="#" style="left:494px">FAQ</a>
    <a href="#" style="left:557px">GALLERY</a>
    <a href="#" style="left:654px">INQUIRIES</a>
    <a href="#" style="left:759px">SHOP</a>
  </nav>
  <a class="nav-contact">CONTACT</a>
  <svg class="header-icon" style="left:1010px" width="28" height="28" viewBox="0 0 28 28" fill="none" stroke="#fff" stroke-width="2"><circle cx="14" cy="14" r="12"/><circle cx="14" cy="11" r="4.5"/><path d="M6 22c2-4 5-5 8-5s6 1 8 5"/></svg>
  <svg class="header-icon" style="left:1058px" width="32" height="28" viewBox="0 0 32 28" fill="none" stroke="#fff" stroke-width="2"><path d="M1 3h5l4 15h16l4-11H8"/><circle cx="12" cy="24" r="2"/><circle cx="24" cy="24" r="2"/><path d="M13 10v5M17 10v5M21 10v5M25 10v5"/></svg>
</header>
<div class="brand-badge"><span>THE<br>GILDED<br>VIPER</span></div>

<section class="hero">
  <div class="hero-visual" role="img" aria-label="Tattoo artist in black gloves working with a tattoo machine"></div>
  <h1 class="hero-title">THE GILDED<br>VIPER</h1>
  <a class="btn-quote">GET A QUOTE</a>
  <div class="slider-dot"></div>
  <div class="social-rail">
    <div class="diamond"></div>
    <div class="sq" style="top:341px"></div>
    <div class="sq" style="top:385px"></div>
  </div>
  <div class="scroll-line"></div>
  <div class="scroll-label">SCROLL DOWN</div>
  <svg class="abs" style="left:1133px;top:612px" width="24" height="36" viewBox="0 0 24 36"><rect x="5" y="3" width="14" height="14" fill="#b5802a" transform="rotate(45 12 10)"/><path d="M12 6v26M5 25l7 7 7-7" stroke="#fff" stroke-width="2" fill="none"/></svg>
</section>

<section class="about">
  <h2 class="section-title" style="left:112px;top:786px">ABOUT US</h2>
  <div class="copy" style="left:112px;top:858px">
    <p>Lorem ipsum dolor sit amet, consectetur adipiscing elit, sed do eiusmod tempor incididunt ut labore et dolore magna aliqua. Ut enim ad minim veniam, quis nostrud exercitation ullamco laboris nisi ut aliquip ex ea commodo consequat. Duis aute irure dolor in reprtempor incididunt ut labore et dolore magna aliqua ehenderit.</p>
    <p>Lorem ipsum dolor sit amet, consectetur adipiscing elit, sed do eiusmod tempor incididunt ut labore et dolore magna aliqua. Ut enim ad minim veniam, quis nostrud exercitation ullamco laboris.</p>
  </div>
  <a class="learn-more" style="left:112px;top:1124px">LEARN MORE
    <svg width="34" height="24" viewBox="0 0 34 24"><rect x="14" y="4" width="16" height="16" fill="#b5802a" transform="rotate(45 22 12)"/><path d="M2 12h24M19 6l7 6-7 6" stroke="#fff" stroke-width="2" fill="none"/></svg>
  </a>
  <div class="gold-frame" style="left:739px;top:725px;width:349px;height:460px"></div>
  <div class="photo" style="left:705px;top:759px;width:348px;height:461px;background:radial-gradient(ellipse at 55% 40%,#3d3a37,#1a1a1a 75%)" role="img" aria-label="Gloved hand holding a rotary tattoo machine"></div>
</section>

<section class="custom">
  <div class="gold-frame" style="left:112px;top:1324px;width:349px;height:461px"></div>
  <div class="photo" style="left:145px;top:1359px;width:351px;height:461px;background:linear-gradient(160deg,#5a5550,#2b2826 55%,#5e5a55)" role="img" aria-label="Artist tattooing an arm with a wrapped tattoo machine"></div>
  <h2 class="section-title" style="left:591px;top:1387px">CUSTOM TATOO</h2>
  <div class="copy" style="left:591px;top:1458px">
    <p>Lorem ipsum dolor sit amet, consectetur adipiscing elit, sed do eiusmod tempor incididunt ut labore et dolore magna aliqua. Ut enim ad minim veniam, quis nostrud exercitation ullamco laboris nisi ut aliquip ex ea commodo consequat. Duis aute irure dolor in reprtempor incididunt ut labore et dolore magna aliqua ehenderit.</p>
    <p>Lorem ipsum dolor sit amet, consectetur adipiscing elit, sed do eiusmod tempor incididunt ut labore et dolore magna aliqua. Ut enim ad minim veniam, quis nostrud exercitation ullamco laboris.</p>
  </div>
  <a class="learn-more" style="left:591px;top:1724px">LEARN MORE
    <svg width="34" height="24" viewBox="0 0 34 24"><rect x="14" y="4" width="16" height="16" fill="#b5802a" transform="rotate(45 22 12)"/><path d="M2 12h24M19 6l7 6-7 6" stroke="#fff" stroke-width="2" fill="none"/></svg>
  </a>
</section>

<section class="featured">
  <div class="products-band"></div>
  <h2 class="section-title" style="left:0;width:1200px;text-align:center;top:2016px">FEATURED PRODUCTS</h2>
  <div class="product-card" style="left:112px"><div class="garment" role="img" aria-label="Black studio t-shirt"></div></div>
  <div class="product-card" style="left:360px"><div class="garment" role="img" aria-label="Black studio hoodie"></div></div>
  <div class="product-card" style="left:609px"><div class="garment" role="img" aria-label="Black studio t-shirt"></div></div>
  <div class="product-card" style="left:858px"><div class="garment" role="img" aria-label="Black studio hoodie"></div></div>
  <div class="product-name" style="left:112px">LOREM IPSUM DOL</div>
  <div class="product-name" style="left:360px">LOREM IPSUM DOL</div>
  <div class="product-name" style="left:609px">LOREM IPSUM DOL</div>
  <div class="product-name" style="left:858px">LOREM IPSUM DOL</div>
  <div class="product-price" style="left:112px">$19.99</div>
  <div class="product-price" style="left:360px">$19.99</div>
  <div class="product-price" style="left:609px">$19.99</div>
  <div class="product-price" style="left:858px">$19.99</div>
</section>

<section class="gallery">
  <h2 class="section-title" style="left:0;width:1200px;text-align:center;top:2609px">OUR GALLERY</h2>
  <div class="photo" style="left:112px;top:2705px;width:230px;height:179px;background:linear-gradient(135deg,#2a2230,#7a4a3a)" role="img" aria-label="Gloved artist tattooing a hand"></div>
  <div class="photo" style="left:360px;top:2705px;width:231px;height:179px;background:linear-gradient(135deg,#1e2a30,#7a4538)" role="img" aria-label="Colour tattoo being inked on skin"></div>
  <div class="photo" style="left:609px;top:2705px;width:231px;height:179px;background:linear-gradient(135deg,#6b6a3a,#c88a4a 50%,#7a2a2a)" role="img" aria-label="Tattooed man sitting outdoors at sunset"></div>
  <div class="photo" style="left:858px;top:2705px;width:230px;height:377px;background:linear-gradient(180deg,#a08a6a,#d8cfc8 60%,#e6e0e4)" role="img" aria-label="Rose tattoo on the back of a neck"></div>
  <div class="photo" style="left:112px;top:2903px;width:479px;height:179px;background:linear-gradient(100deg,#8a7a70,#3a3230 50%,#7a5a4a)" role="img" aria-label="Close-up of a tattoo machine at work"></div>
  <div class="photo" style="left:609px;top:2903px;width:231px;height:179px;background:linear-gradient(120deg,#2a2220,#6a4a40)" role="img" aria-label="Artist tattooing a client's shoulder"></div>
</section>

<footer class="site-footer"></footer>
<nav class="footer-nav">
  <a href="#" style="left:112px">ABOUT</a>
  <a href="#" style="left:204px">FAQ</a>
  <a href="#" style="left:278px">GALLERY</a>
  <a href="#" style="left:823px">INQUIRIES</a>
  <a href="#" style="left:928px">SHOP</a>
  <a href="#" style="left:1003px">CONTACT US</a>
</nav>
<div class="footer-brand">THE<br>GILDED<br>VIPER</div>
<div class="hr" style="left:112px;top:3322px;width:398px"></div>
<div class="hr" style="left:690px;top:3322px;width:398px"></div>
<div class="vr" style="left:437px;top:3322px;height:214px"></div>
<div class="vr" style="left:763px;top:3322px;height:214px"></div>

<div class="contact-col" style="left:110px;top:3372px">
  <svg width="26" height="28" viewBox="0 0 26 28" fill="none" stroke="#b5802a" stroke-width="2"><path d="M13 22s-7-7-7-12a7 7 0 0 1 14 0c0 5-7 12-7 12z"/><circle cx="13" cy="10" r="2.5"/><ellipse cx="13" cy="24" rx="9" ry="2.5"/></svg>
  <h4>LOCATION:</h4>
  <p>465, Lorum Ipsum Dolore Sed Do,<br>United States</p>
</div>
<div class="contact-col" style="left:440px;top:3421px">
  <svg width="26" height="26" viewBox="0 0 26 26" fill="none" stroke="#b5802a" stroke-width="2"><path d="M6 3l4 5-2 3c1 3 4 6 7 7l3-2 5 4-2 3c-8 1-17-8-18-17z"/><path d="M15 4a7 7 0 0 1 7 7M15 8a3 3 0 0 1 3 3"/></svg>
  <h4>PHONE:</h4>
  <p>+1 (000) 000 0000</p>
</div>
<div class="contact-col" style="left:763px;top:3372px">
  <svg width="28" height="26" viewBox="0 0 28 26" fill="none" stroke="#b5802a" stroke-width="2"><path d="M3 10l11-8 11 8v13H3z"/><path d="M3 10l11 8 11-8"/><circle cx="14" cy="10" r="3"/></svg>
  <h4>EMAIL:</h4>
  <p>info@thegildedviper.com</p>
</div>

<div class="hr" style="left:112px;top:3537px;width:976px"></div>
<div class="copyright">© 2023 <b>THE GILDED VIPER</b> &nbsp;|&nbsp; All Rights Reserved</div>
<div class="foot-social" style="left:974px;background:var(--gold)"></div>
<div class="foot-social" style="left:1016px;border:1.5px solid #fff"></div>
<div class="foot-social" style="left:1058px;border:1.5px solid #fff"></div>

</body>
</html>
```